I need a audit of my current site.. with suggestions and actions

My current site, www.brightgridworks does not support the high tech industry we are in. I am seeking knowledge, direction and action, I will pay hourly or by job. I also need SEO help, driven with impact trusted deliverable, our clients have to trust us to do our job. We are like Voltrex to the construction industry, gathering their data for the lifecycle. Eliminating litigation, un wanted change orders and providing audit ready projects. Eveyone wins

Target Market(s)

Construction industry, Federal and Private

Industry/Entity Type

Construction industry, globally

Coding

Coded - Design and coding required

Number of Pages Required

5+ page

Font styles to use
Sans Serif

Colors
EE7325
F08F49
F5BC92
FAE3D3
FDF4ED

Requirements
Must have
• High tech look
Should not have
• Misspelled words

```html
<!DOCTYPE html>
<html lang="en">
<head>
<meta charset="utf-8">
<title>BrightGridWorks – The Smartest Way to Build</title>
<link href="https://fonts.googleapis.com/css2?family=Roboto:wght@300;400;500;700&display=swap" rel="stylesheet">
<style>
:root{
  --orange:#EE7325;
  --orange-deep:#F15A0A;
  --orange-mid:#F08F49;
  --peach:#F5BC92;
  --cream:#FAE3D3;
  --ivory:#FDF4ED;
  --ink:#222222;
  --text:#555555;
  --dark:#1b1b1b;
  --charcoal:#3a3a3a;
  --white:#ffffff;
}
*{margin:0;padding:0;box-sizing:border-box}
html,body{width:1200px;height:4934px;overflow:hidden}
body{font-family:"Roboto",sans-serif;color:var(--ink);background:var(--white);position:relative}
.abs{position:absolute}
.rule{width:70px;height:3px;background:var(--orange);margin:0 auto 22px}
.section-title{font-weight:300;font-size:40px;text-align:center;line-height:1.3}

/* header */
.site-header{top:0;left:0;width:1200px;height:110px;background:var(--white)}
.call-bar{top:0;right:0;width:355px;height:32px;background:var(--orange);color:#fff;font-size:14px;display:flex;align-items:center;padding-left:42px;gap:8px;clip-path:polygon(0 0,100% 0,100% 100%,24px 100%)}
.brand{top:42px;left:110px;display:flex;align-items:center;gap:8px}
.brand-name{font-size:30px;font-weight:300;color:var(--orange)}
.brand-mark{width:14px;height:14px;background:var(--orange)}
.main-nav{top:58px;left:414px;display:flex;gap:22px;font-size:14px;color:var(--ink)}
.main-nav .active{color:var(--orange);border-bottom:2px solid var(--orange);padding-bottom:4px}
.nav-tools{top:58px;left:962px;display:flex;align-items:center;gap:24px;font-size:14px}
.nav-tools .sep{width:1px;height:26px;background:#ddd}

/* hero */
.hero{top:110px;left:0;width:1200px;height:600px;background:linear-gradient(120deg,#3c3a36 0%,#5c5a55 40%,#2d3138 75%,#1e2329 100%)}
.hero-copy{top:268px;left:0;width:1200px;text-align:center;color:#fff}
.hero-copy h1{font-weight:300;font-size:43px;letter-spacing:1px}
.hero-copy p{font-size:13px;margin-top:18px;line-height:26px}
.hero-copy .tag{color:var(--orange);font-weight:700;font-size:24px;margin-top:10px}
.hero-arrow{top:332px;width:40px;height:70px}

/* about */
.about-card{top:518px;left:169px;width:862px;height:507px;background:#fff;border-radius:22px;box-shadow:0 8px 30px rgba(0,0,0,.15);padding:48px 60px}
.about-card h2{font-weight:300;font-size:38px;text-align:center}
.about-card .lead{font-size:13.5px;line-height:26px;color:var(--text);text-align:center;margin:14px 0 18px}
.about-body{display:flex;gap:38px}
.about-photo{width:370px;height:224px;border-radius:14px;background:linear-gradient(160deg,#9eb6d8,#6d6b6a 55%,#c9a27e)}
.checklist{list-style:none;font-size:13.5px;color:var(--text)}
.checklist li{display:flex;align-items:center;gap:16px;height:39px}
.checklist li::before{content:"✓";width:13px;height:13px;border-radius:50%;background:var(--orange);color:#fff;font-size:9px;display:flex;align-items:center;justify-content:center}

/* platforms */
.platforms{top:1120px;left:0;width:1200px}
.logo-row{top:1305px;left:0;width:1200px;height:130px}
.logo-tile{top:0;width:136px;height:136px;display:flex;align-items:center;justify-content:center}
.logo-tile::before{content:"";position:absolute;inset:18px;transform:rotate(45deg);border-radius:22px;background:#fff;box-shadow:0 4px 16px rgba(0,0,0,.1)}
.logo-tile.featured::before{border:3px solid var(--orange)}
.logo-tile span{position:relative;font-weight:700;font-size:21px;color:var(--ink)}
.logo-tile.featured span{color:var(--orange)}
.row-arrow{top:1358px;width:20px;height:24px}

/* services */
.services{top:1470px;left:0;width:1200px;height:1290px;background:var(--orange-deep)}
.services-title{top:1720px;left:0;width:1200px;color:#fff}
.services-title .rule{background:#fff}
.card{width:307px;height:376px;background:#fff;border-radius:6px;box-shadow:0 6px 20px rgba(0,0,0,.15);text-align:center;padding:26px 38px 0}
.card svg{width:64px;height:64px}
.card h3{font-size:19px;font-weight:700;margin:18px 0 18px}
.card p{font-size:12.8px;line-height:25.5px;color:var(--text);height:128px;overflow:hidden}
.btn-ask{display:inline-block;margin-top:28px;border:2px solid var(--orange);border-radius:20px;width:138px;height:38px;line-height:34px;font-size:12px;font-weight:700;color:var(--ink)}

/* milestones */
.milestones{top:2735px;left:0;width:1200px;height:640px;background:linear-gradient(120deg,#2a2c33,#454850 45%,#2e3440 80%,#262b35)}
.milestones-title{top:2945px;left:0;width:1200px;color:#fff}
.milestones-title .rule{background:#fff}
.stat{top:3062px;width:250px;text-align:center;color:#fff}
.stat .ring{width:96px;height:96px;border-radius:50%;background:var(--orange);margin:0 auto;display:flex;align-items:center;justify-content:center;font-size:32px;font-weight:700}
.stat .ring.small{font-size:26px}
.stat p{font-size:16px;margin-top:22px}

/* contact */
.contact-title{top:3515px;left:0;width:1200px}
.map{top:3604px;left:111px;width:474px;height:408px;background:linear-gradient(135deg,#e6eae3,#d7dfe8 50%,#ebe7dd)}
.map-card{top:3610px;left:117px;width:215px;height:88px;background:#fff;box-shadow:0 1px 4px rgba(0,0,0,.25);padding:10px;font-size:10px;line-height:14px;color:var(--text)}
.map-card b{color:var(--ink);font-size:11px}
.map-card .link{color:#1a73e8;margin-top:6px;display:block}
.form-panel{top:3604px;left:600px;width:489px;height:408px;background:#E8601E;padding:24px 32px;color:#fff}
.form-panel h4{font-size:21px;font-weight:700;margin-bottom:20px}
.field-row{display:flex;gap:18px;margin-bottom:16px}
.field{flex:1;height:38px;background:#fff;border-radius:6px;color:#777;font-size:12px;padding:11px 16px}
.field.area{height:134px}
.btn-submit{margin-top:20px;width:202px;height:38px;border-radius:19px;background:var(--charcoal);color:#fff;font-size:12px;font-weight:700;display:flex;align-items:center;justify-content:center}

/* footer */
.footer{top:4040px;left:0;width:1200px;height:894px;background:var(--dark)}
.info-box{top:4275px;width:307px;height:140px;background:#232323;border-radius:6px;padding:36px 0 0 98px;color:#fff}
.info-box .icon{position:absolute;left:34px;top:36px;width:40px;height:40px;border-radius:50%;background:var(--orange);display:flex;align-items:center;justify-content:center}
.info-box h5{font-size:20px;font-weight:400;margin-bottom:14px}
.info-box p{font-size:15px;line-height:25px}
.info-box p.mail{font-size:13.5px}
.foot-col{top:4480px;color:#fff}
.foot-col h6{font-size:20px;font-weight:700;margin-bottom:26px}
.foot-col ul{list-style:none;font-size:13.5px;line-height:26px}
.foot-col li::before{content:"»";margin-right:14px}
.badge{background:#fff;border-radius:50%}
.copyright{top:4705px;left:0;width:1200px;text-align:center;color:#fff;font-size:13.5px}
.skyline{left:0;top:4770px;width:1200px;height:164px;background:linear-gradient(#1b1b1b,#0c0c0c)}
</style>
</head>
<body>

<header class="abs site-header">
  <div class="abs call-bar">
    <svg width="12" height="12" viewBox="0 0 24 24"><path fill="#fff" d="M6.6 10.8a15.1 15.1 0 006.6 6.6l2.2-2.2c.3-.3.7-.4 1-.2 1.1.4 2.3.6 3.6.6.6 0 1 .4 1 1V20c0 .6-.4 1-1 1C10.6 21 3 13.4 3 4c0-.6.4-1 1-1h3.5c.6 0 1 .4 1 1 0 1.3.2 2.5.6 3.6.1.3 0 .7-.2 1z"/></svg>
    Call us Today : (555) 214-0388
  </div>
  <div class="abs brand"><span class="brand-mark"></span><span class="brand-name">BrightGridWorks</span></div>
  <nav class="abs main-nav">
    <span class="active">Home</span><span>What We Offer</span><span>Portfolio</span><span>About</span><span>Podcast</span><span>Blogs</span>
  </nav>
  <div class="abs nav-tools">
    <svg width="14" height="14" viewBox="0 0 24 24"><circle cx="10" cy="10" r="7" fill="none" stroke="#222" stroke-width="3"/><path d="M15 15l6 6" stroke="#222" stroke-width="3"/></svg>
    <span class="sep"></span>
    <span>&#9679; Login</span>
  </div>
</header>

<section class="abs hero" role="img" aria-label="Photo of a building under construction with tower cranes against the sky"></section>
<svg class="abs" style="top:600px;left:0" width="1200" height="120" viewBox="0 0 1200 120">
  <polygon points="0,20 600,100 1200,20 1200,120 0,120" fill="#F15A0A"/>
  <polygon points="0,50 600,110 1200,50 1200,120 0,120" fill="#3a3a3a"/>
  <polygon points="0,70 600,120 1200,70 1200,120 0,120" fill="#fff"/>
</svg>
<div class="abs hero-copy">
  <h1>THE SMARTEST WAY TO BUILD</h1>
  <p>ORGANIZED AND SECURE &nbsp; / &nbsp; PLANHOLDERS TEAM NOTIFICATIONS AND UPDATES<br>/ &nbsp; SAFEGUARDED AGAINST LITIGATION</p>
  <p class="tag">BUILDING THE ONLY WAY!</p>
</div>
<svg class="abs hero-arrow" style="left:72px" viewBox="0 0 40 70"><path d="M34 4L6 35l28 31" fill="none" stroke="#fff" stroke-width="4"/></svg>
<svg class="abs hero-arrow" style="left:1088px" viewBox="0 0 40 70"><path d="M6 4l28 31L6 66" fill="none" stroke="#fff" stroke-width="4"/></svg>

<article class="abs about-card">
  <div class="rule"></div>
  <h2>About BrightGridWorks</h2>
  <p class="lead">Our clients are seeing an 18 to 1 return on their investment with BrightGridWorks. Our software is paired with a Project Information Manager who improves project transparency, accountability, and ensures informed decision making. Deliver projects on time and under budget.</p>
  <div class="about-body">
    <div class="about-photo" role="img" aria-label="Photo of a worker on a tiled house roof"></div>
    <ul class="checklist">
      <li>Third-party Custodian Of Project Information</li>
      <li>Dedicated Project Information Manager</li>
      <li>Information Governance</li>
      <li>Risk Mitigation</li>
      <li>Audited And Vetted Documentation</li>
      <li>Digital Twin Integration For Facilities Management</li>
    </ul>
  </div>
</article>

<div class="abs platforms">
  <div class="rule"></div>
  <h2 class="section-title">Construction Management<br>Software Platforms</h2>
</div>
<div class="abs logo-row">
  <div class="abs logo-tile" style="left:140px"><span>Planvault</span></div>
  <div class="abs logo-tile" style="left:335px"><span>Modelbase</span></div>
  <div class="abs logo-tile featured" style="left:532px"><span>Siteflow</span></div>
  <div class="abs logo-tile" style="left:727px"><span>Buildcore</span></div>
  <div class="abs logo-tile" style="left:922px"><span>Fieldgrid</span></div>
</div>
<svg class="abs row-arrow" style="left:48px" viewBox="0 0 20 24"><path d="M14 3L5 12l9 9" fill="none" stroke="#222" stroke-width="2.5"/></svg>
<svg class="abs row-arrow" style="left:1134px" viewBox="0 0 20 24"><path d="M6 3l9 9-9 9" fill="none" stroke="#222" stroke-width="2.5"/></svg>

<section class="abs services"></section>
<svg class="abs" style="top:1470px;left:0" width="1200" height="160" viewBox="0 0 1200 160">
  <polygon points="0,0 1200,0 600,110" fill="#fff"/>
  <polygon points="0,0 600,110 1200,0 1200,34 600,150 0,34" fill="#3a3a3a"/>
</svg>
<div class="abs services-title">
  <div class="rule"></div>
  <h2 class="section-title">Best Construction<br>Management Software</h2>
</div>

<div class="abs card" style="top:1873px;left:111px">
  <svg viewBox="0 0 64 64"><circle cx="32" cy="32" r="20" fill="none" stroke="#EE7325" stroke-width="3" stroke-dasharray="6 4"/><circle cx="32" cy="26" r="7" fill="none" stroke="#EE7325" stroke-width="3"/><path d="M20 46c3-8 21-8 24 0" fill="none" stroke="#EE7325" stroke-width="3"/></svg>
  <h3>Project Managers</h3>
  <p>Every BrightGridWorks project comes with a dedicated Project Information Manager. The Project Information Manager (PIM) is at the intersection of all project data.</p>
  <span class="btn-ask">ASK US HOW</span>
</div>
<div class="abs card" style="top:1873px;left:445px">
  <svg viewBox="0 0 64 64"><circle cx="24" cy="24" r="12" fill="none" stroke="#EE7325" stroke-width="3" stroke-dasharray="5 3"/><circle cx="42" cy="42" r="12" fill="none" stroke="#EE7325" stroke-width="3" stroke-dasharray="5 3"/><circle cx="24" cy="24" r="4" fill="#EE7325"/><circle cx="42" cy="42" r="4" fill="#EE7325"/></svg>
  <h3>Integration Across</h3>
  <p>The BrightGridWorks construction project management software handles every phase of your projects. Our superior project management tools are created for</p>
  <span class="btn-ask">ASK US HOW</span>
</div>
<div class="abs card" style="top:1873px;left:780px">
  <svg viewBox="0 0 64 64"><circle cx="38" cy="26" r="16" fill="none" stroke="#EE7325" stroke-width="3"/><path d="M26 38L10 54" stroke="#EE7325" stroke-width="5"/><path d="M31 32V26M37 32V20M43 32V16" stroke="#EE7325" stroke-width="3"/></svg>
  <h3>Remove Data Silos</h3>
  <p>Our world is data-driven. Organizations have data spread out across different departments and silos. Many issues may arise as companies store data within these</p>
  <span class="btn-ask">ASK US HOW</span>
</div>
<div class="abs card" style="top:2275px;left:111px">
  <svg viewBox="0 0 64 64"><rect x="8" y="8" width="16" height="16" rx="4" fill="none" stroke="#EE7325" stroke-width="3"/><rect x="40" y="8" width="16" height="16" rx="4" fill="none" stroke="#EE7325" stroke-width="3"/><rect x="8" y="40" width="16" height="16" rx="4" fill="none" stroke="#EE7325" stroke-width="3"/><rect x="40" y="40" width="16" height="16" rx="4" fill="none" stroke="#EE7325" stroke-width="3"/><circle cx="32" cy="32" r="6" fill="none" stroke="#EE7325" stroke-width="3"/></svg>
  <h3>Digital Twin of Your</h3>
  <p>Every job you do is important. Maintaining documents for each completed construction project is essential, but a real hassle. BrightGridWorks creates the digital</p>
  <span class="btn-ask">ASK US HOW</span>
</div>
<div class="abs card" style="top:2275px;left:445px">
  <svg viewBox="0 0 64 64"><circle cx="32" cy="26" r="13" fill="none" stroke="#EE7325" stroke-width="3"/><text x="32" y="32" text-anchor="middle" font-size="16" font-weight="700" fill="#EE7325" font-family="Roboto,sans-serif">$</text><path d="M6 52h14l10 4 22-8" fill="none" stroke="#EE7325" stroke-width="3"/><path d="M32 4v5M22 7l2 4M42 7l-2 4" stroke="#EE7325" stroke-width="3"/></svg>
  <h3>Return on Investment</h3>
  <p>Every BrightGridWorks project comes with a dedicated Project Information Manager. The Project Information Manager (PIM) is at the intersection of all project data.</p>
  <span class="btn-ask">ASK US HOW</span>
</div>
<div class="abs card" style="top:2275px;left:780px">
  <svg viewBox="0 0 64 64"><rect x="8" y="14" width="26" height="42" rx="3" fill="none" stroke="#EE7325" stroke-width="3"/><path d="M14 26h14M14 34h14M14 42h10" stroke="#EE7325" stroke-width="3"/><circle cx="42" cy="38" r="14" fill="none" stroke="#EE7325" stroke-width="3"/><circle cx="42" cy="38" r="7" fill="#EE7325"/></svg>
  <h3>Here is the Proof</h3>
  <p>BrightGridWorks has created visibility where there has not been in the past, especially for federal owners. Because we audit, organize, and present project information in one</p>
  <span class="btn-ask">ASK US HOW</span>
</div>

<section class="abs milestones" role="img" aria-label="Photo of a modern office building at dusk"></section>
<svg class="abs" style="top:2735px;left:0" width="1200" height="90" viewBox="0 0 1200 90">
  <polygon points="0,0 1200,0 1200,10 600,80 0,10" fill="#F15A0A"/>
</svg>
<svg class="abs" style="top:3220px;left:0" width="1200" height="160" viewBox="0 0 1200 160">
  <polygon points="0,20 600,120 1200,20 1200,160 0,160" fill="#F15A0A"/>
  <polygon points="0,50 600,140 1200,50 1200,160 0,160" fill="#3a3a3a"/>
  <polygon points="0,75 600,160 1200,75 1200,160 0,160" fill="#fff"/>
</svg>
<div class="abs milestones-title">
  <div class="rule"></div>
  <h2 class="section-title">Milestones</h2>
</div>
<div class="abs stat" style="left:150px"><div class="ring">16</div><p>YEARS IN BUSINESS</p></div>
<div class="abs stat" style="left:475px"><div class="ring">+2K</div><p>PROJECTS COMPLETED</p></div>
<div class="abs stat" style="left:800px"><div class="ring small">$23B</div><p>CONSTRUCTION VALUE</p></div>

<div class="abs contact-title">
  <div class="rule"></div>
  <h2 class="section-title">Contact Us</h2>
</div>
<div class="abs map" role="img" aria-label="Street map showing the office location"></div>
<div class="abs map-card">
  <b>410 Meridian Ave</b><br>410 Meridian Ave, Riverton, KS 66000, USA
  <span class="link">View larger map</span>
</div>
<div class="abs form-panel">
  <h4>REQUEST A FREE CONSULTATION</h4>
  <div class="field-row"><div class="field">First name*</div><div class="field">Last name*</div></div>
  <div class="field-row"><div class="field">Email*</div><div class="field">Phone*</div></div>
  <div class="field-row"><div class="field area">Tell me about your case*</div></div>
  <div class="btn-submit">SUBMIT NOW</div>
</div>

<footer class="abs footer"></footer>
<svg class="abs" style="top:4030px;left:0" width="1200" height="180" viewBox="0 0 1200 180">
  <polygon points="0,0 1200,0 1200,20 600,150 0,20" fill="#fff"/>
  <polygon points="0,20 600,150 1200,20 1200,40 600,170 0,40" fill="#F15A0A"/>
</svg>
<div class="abs info-box" style="left:111px">
  <span class="icon"><svg width="16" height="20" viewBox="0 0 16 20"><path d="M8 0a8 8 0 00-8 8c0 6 8 12 8 12s8-6 8-12a8 8 0 00-8-8z" fill="#fff"/><circle cx="8" cy="8" r="3" fill="#EE7325"/></svg></span>
  <h5>Location:</h5><p>410 Meridian Avenue<br>Riverton, KS 66000</p>
</div>
<div class="abs info-box" style="left:447px">
  <span class="icon"><svg width="18" height="18" viewBox="0 0 24 24"><path fill="#fff" d="M6.6 10.8a15.1 15.1 0 006.6 6.6l2.2-2.2c.3-.3.7-.4 1-.2 1.1.4 2.3.6 3.6.6.6 0 1 .4 1 1V20c0 .6-.4 1-1 1C10.6 21 3 13.4 3 4c0-.6.4-1 1-1h3.5c.6 0 1 .4 1 1 0 1.3.2 2.5.6 3.6.1.3 0 .7-.2 1z"/></svg></span>
  <h5>Phone:</h5><p>(555) 214-0388</p>
</div>
<div class="abs info-box" style="left:782px">
  <span class="icon"><svg width="18" height="14" viewBox="0 0 18 14"><rect width="18" height="14" rx="2" fill="#fff"/><path d="M1 2l8 6 8-6" fill="none" stroke="#EE7325" stroke-width="2"/></svg></span>
  <h5>Email:</h5><p class="mail">hello@brightgridworks.com<br>support@brightgridworks.com</p>
</div>

<div class="abs foot-col" style="left:110px"><h6>How We Work For You</h6><ul><li>Owners / Shareholders</li><li>Contractors</li><li>Construction Lawyers</li><li>Finance</li></ul></div>
<div class="abs foot-col" style="left:414px"><h6>Legal</h6><ul><li>Privacy policy</li><li>Terms &amp; Conditions</li><li>Disclaimer</li><li>Support</li></ul></div>
<div class="abs foot-col" style="left:641px"><h6>Quick Links</h6><ul><li>What We Offer</li><li>Portfolio</li><li>About</li><li>Podcast</li></ul></div>
<div class="abs badge" style="top:4480px;left:872px;width:92px;height:92px"></div>
<div class="abs badge" style="top:4480px;left:978px;width:92px;height:92px"></div>
<div class="abs" style="top:4582px;left:846px;width:230px;height:44px;background:#fff;border-radius:6px"></div>

<div class="abs copyright">Copyright © 2022 Companyname. All Rights Reserved.</div>
<div class="abs skyline" role="img" aria-label="Dark city skyline silhouette"></div>

</body>
</html>
```